Web Design for a Biotech Consulting Firm

We need a web site design for a new business based in Philadelphia called Verantel Dx. This is a consulting firm that will serve medical diagnostics industry, which is part of the life science/healthcare industry focusing on developing and marketing products that help in early detection, monitoring or management of diseases. Our consulting firm will help medical diagnostic companies to overcome key challenges in designing, evaluating and marketing new products.Our company name is Verantel Dx. Verantel is Latin word for "something" Dx represents diagnostics. The idea behind the name is that we help companies to transform the original, early product ideas ("nothing") into "something"; which is a product with full clinical utility that will help to improve health and well-being.The web site should use the visual feel of the logo (attached), be modern, simple and clean looking and represent creativity, innovation, scientific thinking and progress.
Updates

Wix Design is acceptable

Industry/Entity Type

Biotechnology

Coding

Coded - Design and coding required

Number of Pages Required

1 page

Font styles to use
Sans Serif

Requirements
Must have
• simple, clean look couple of pages
Should not have
• a lot of pages

```html
<!DOCTYPE html>
<html lang="en">
<head>
<meta charset="utf-8">
<title>Verantel Dx</title>
<link href="https://fonts.googleapis.com/css2?family=Montserrat:wght@400;500;600;700;800&display=swap" rel="stylesheet">
<style>
:root{
  --blue:#1a6cf0;
  --ink:#1b1b1b;
  --text:#333;
  --grey:#e6e6e6;
  --soft:#f2f2f2;
  --line:#dcdcdc;
  --white:#fff;
}
*{margin:0;padding:0;box-sizing:border-box}
html,body{width:1200px;height:3044px;overflow:hidden}
body{font-family:'Montserrat',sans-serif;color:var(--text);background:var(--white);position:relative}
.abs{position:absolute}
.center{text-align:center}
.btn{display:flex;align-items:center;justify-content:center;background:var(--blue);color:var(--white);font-weight:700;font-size:14px;letter-spacing:.3px}

/* header */
.header{left:0;top:0;width:1200px;height:134px;background:var(--white)}
.logo-name{left:104px;top:58px;font-size:25px;font-weight:500;color:var(--ink);white-space:nowrap}
.nav{top:60px;font-size:14px;font-weight:500;color:var(--ink);letter-spacing:.2px}
.nav-mark{left:604px;top:132px;width:58px;height:2px;background:#999}

/* hero */
.hero{left:0;top:134px;width:1200px;height:613px;background:linear-gradient(135deg,#8f959c 0%,#a7abb1 35%,#7d828a 65%,#4d5158 100%)}
.hero-title{left:0;width:1200px;top:352px;font-size:36px;font-weight:700;color:var(--white);text-shadow:0 1px 3px rgba(0,0,0,.35)}
.hero-sub{left:0;width:1128px;top:408px;font-size:18px;color:var(--white);text-shadow:0 1px 3px rgba(0,0,0,.45)}
.hero-btn{left:521px;top:451px;width:158px;height:36px}
.dot{top:585px;width:10px;height:10px;border-radius:50%;background:var(--white)}
.dot.on{background:var(--ink);border:2px solid var(--white)}

/* about */
.about-photo{left:0;top:747px;width:601px;height:536px;background:linear-gradient(160deg,#c7d4e3 0%,#eef2f6 45%,#8fa6c2 100%)}
.about-panel{left:603px;top:672px;width:597px;height:501px;background:var(--blue);color:var(--white)}
.about-bar{left:266px;top:96px;width:64px;height:6px;background:var(--white)}
.about-title{left:0;width:597px;top:128px;font-size:43px;font-weight:700}
.about-copy{left:60px;width:477px;top:214px;font-size:15.5px;line-height:33px}

/* services */
.section-title{left:0;width:1200px;font-size:42px;font-weight:700;color:var(--ink)}
.card{top:1478px;width:333px;height:400px;background:var(--white);box-shadow:0 0 4px rgba(0,0,0,.3)}
.card-foot{left:0;top:270px;width:333px;height:130px;background:var(--grey)}
.card-name{left:0;width:333px;top:33px;font-size:17px;font-weight:500;color:var(--ink)}
.card-btn{left:87px;top:57px;width:158px;height:36px}
.card svg{position:absolute;left:86px;top:52px}

/* blog */
.post-img{top:2023px;width:246px;height:211px}
.post-title{font-size:18.5px;font-weight:600;color:var(--ink);line-height:32px;width:230px}
.post-meta{font-size:14px;color:var(--text)}
.post-date{width:104px;height:28px;background:var(--ink);color:var(--white);font-size:14px;display:flex;align-items:center;justify-content:center}
.post-link{font-size:14px;font-weight:700;color:var(--blue);text-decoration:underline}

/* testimonials */
.testi{left:0;top:2325px;width:1200px;height:447px;background:var(--soft)}
.testi-bar{left:568px;top:81px;width:64px;height:6px;background:#777}
.testi-title{left:0;width:1200px;top:110px;font-size:42px;font-weight:700;color:var(--ink)}
.quote{left:190px;width:820px;top:200px;font-size:24px;line-height:34px;color:var(--ink)}
.posted{left:0;width:1200px;top:326px;font-size:17px;color:var(--ink)}

/* footer */
.footer{left:0;top:2772px;width:1200px;height:188px;border-bottom:1px solid var(--line)}
.fcol{top:0;height:188px;border-right:1px solid var(--line)}
.foot-h{font-size:17px;font-weight:500;color:var(--ink)}
.social{top:111px;width:14px;height:14px;border-radius:50%;background:var(--ink)}
.flink{font-size:14px;color:var(--ink);line-height:28px}
.email{left:790px;top:98px;width:238px;height:43px;border:1px solid var(--line);font-size:11px;color:#aaa;display:flex;align-items:center;padding-left:16px;background:var(--white)}
.submit{left:1035px;top:98px;width:90px;height:43px}
.copy{left:0;width:1200px;top:2989px;font-size:14px;color:var(--ink)}
</style>
</head>
<body>

<header class="abs header">
  <div class="abs logo-name">Verantel Dx</div>
  <nav>
    <span class="abs nav" style="left:394px">HOME</span>
    <span class="abs nav" style="left:473px">ABOUT US</span>
    <span class="abs nav" style="left:581px">SERVICES &amp; PRODUCTS</span>
    <span class="abs nav" style="left:785px">TESTIMONIALS</span>
    <span class="abs nav" style="left:924px">BLOG</span>
    <span class="abs nav" style="left:999px">CONTACT</span>
    <svg class="abs" style="left:1109px;top:62px" width="14" height="14" viewBox="0 0 14 14"><circle cx="5.5" cy="5.5" r="4" fill="none" stroke="#1b1b1b" stroke-width="2.2"/><line x1="8.5" y1="8.5" x2="13" y2="13" stroke="#1b1b1b" stroke-width="2.6"/></svg>
  </nav>
  <div class="abs nav-mark"></div>
</header>

<section class="abs hero" role="img" aria-label="Doctors meeting around a table with clipboards, an x-ray and a laptop"></section>
<h1 class="abs hero-title center">VERANTEL DX</h1>
<p class="abs hero-sub center">Sed ut perspiciatis unde omnis iste natus .</p>
<div class="abs btn hero-btn">READ MORE</div>
<span class="abs dot" style="left:552px"></span>
<span class="abs dot on" style="left:580px"></span>
<span class="abs dot" style="left:609px"></span>
<span class="abs dot" style="left:638px"></span>

<section>
  <div class="abs about-photo" role="img" aria-label="Scientists working together in a laboratory"></div>
  <div class="abs about-panel">
    <div class="abs about-bar"></div>
    <h2 class="abs about-title center">VERANTEL DX</h2>
    <p class="abs about-copy center">Sed ut perspiciatis unde omnis iste natus error sit voluptatem accusantium doloremque laudantium, totam rem aperiam, eaque ipsa quae ab illo inventore veritatis et quasi architecto beatae vitae dicta sunt explicabo. Nemo enim ipsam voluptatem quia voluptas sit aspernatur aut odit aut fugit, sed quia consequuntur magni dolores</p>
  </div>
</section>

<h2 class="abs section-title center" style="top:1370px">OUR SERVICES</h2>

<div class="abs card" style="left:73px">
  <svg width="160" height="160" viewBox="0 0 160 160" fill="none" stroke="#1a6cf0" stroke-width="7" stroke-linecap="round">
    <path d="M32 8 C32 50 128 60 128 150"/><path d="M128 8 C128 50 32 60 32 150"/>
    <line x1="40" y1="22" x2="120" y2="22"/><line x1="50" y1="40" x2="110" y2="40"/><line x1="62" y1="56" x2="98" y2="56"/>
    <line x1="62" y1="104" x2="98" y2="104"/><line x1="50" y1="120" x2="110" y2="120"/><line x1="40" y1="138" x2="120" y2="138"/>
  </svg>
  <div class="abs card-foot"><div class="abs card-name center">BIOTECH</div><div class="abs btn card-btn">READ MORE</div></div>
</div>
<div class="abs card" style="left:434px">
  <svg width="160" height="160" viewBox="0 0 160 160" fill="none" stroke="#1a6cf0" stroke-width="7" stroke-linejoin="round">
    <rect x="30" y="8" width="30" height="12"/><path d="M36 20 V56 C10 70 6 95 14 118 C22 140 68 140 76 118 C84 95 80 70 54 56 V20"/>
    <path d="M12 100 C30 92 55 108 80 100"/>
    <path d="M100 14 H148 V30 L140 40 V146 H100 Z"/>
    <line x1="100" y1="60" x2="118" y2="60"/><line x1="100" y1="82" x2="118" y2="82"/><line x1="100" y1="104" x2="118" y2="104"/><line x1="100" y1="126" x2="118" y2="126"/>
  </svg>
  <div class="abs card-foot"><div class="abs card-name center">CLINICAL UTILITY</div><div class="abs btn card-btn">READ MORE</div></div>
</div>
<div class="abs card" style="left:794px">
  <svg width="160" height="160" viewBox="0 0 160 160" fill="none" stroke="#1a6cf0" stroke-width="7" stroke-linecap="round">
    <path d="M26 100 V16 a12 12 0 0 1 24 0 V100 a26 26 0 1 1 -24 0 Z"/><circle cx="38" cy="124" r="11"/>
    <line x1="62" y1="22" x2="72" y2="22"/><line x1="62" y1="40" x2="72" y2="40"/><line x1="62" y1="58" x2="72" y2="58"/><line x1="62" y1="76" x2="72" y2="76"/>
    <rect x="92" y="4" width="44" height="148" rx="22"/><rect x="104" y="22" width="20" height="52" rx="10"/>
    <line x1="108" y1="40" x2="120" y2="40"/><line x1="108" y1="56" x2="120" y2="56"/>
  </svg>
  <div class="abs card-foot"><div class="abs card-name center">MEDICAL DEVICES</div><div class="abs btn card-btn">READ MORE</div></div>
</div>

<h2 class="abs section-title center" style="top:1923px">BLOG</h2>

<article>
  <div class="abs post-img" style="left:81px;background:linear-gradient(135deg,#e9eef3,#b8c5d4 60%,#5d6e86)" role="img" aria-label="Researcher looking into a microscope"></div>
  <h3 class="abs post-title" style="left:352px;top:2024px">SED UT PERSPICIATIS VOLUPTATEM</h3>
  <p class="abs post-meta" style="left:352px;top:2100px">Ut enim ad minima veniam,</p>
  <p class="abs post-meta" style="left:352px;top:2131px">MALAYSIA</p>
  <div class="abs post-date" style="left:353px;top:2162px">31 Aug 2018</div>
  <a class="abs post-link" style="left:354px;top:2212px">Read more</a>
</article>
<article>
  <div class="abs post-img" style="left:626px;background:linear-gradient(135deg,#2f6f86,#8fc3d3 55%,#1f4d63)" role="img" aria-label="Medical researcher using a holographic display"></div>
  <h3 class="abs post-title" style="left:897px;top:2024px">SED UT PERSPICIATIS VOLUPTATEM</h3>
  <p class="abs post-meta" style="left:898px;top:2100px">Ut enim ad minima veniam,</p>
  <p class="abs post-meta" style="left:898px;top:2131px">MALAYSIA</p>
  <div class="abs post-date" style="left:899px;top:2162px">31 Aug 2018</div>
  <a class="abs post-link" style="left:900px;top:2212px">Read more</a>
</article>

<section class="abs testi">
  <div class="abs testi-bar"></div>
  <h2 class="abs testi-title center">TESTIMONIALS</h2>
  <svg class="abs" style="left:117px;top:211px" width="14" height="20" viewBox="0 0 14 20"><path d="M11 2 L3 10 L11 18" fill="none" stroke="#1b1b1b" stroke-width="3.5"/></svg>
  <p class="abs quote center">“Lorem ipsum dolor sit amet, consectetur adipiscing elit, sed do eiusmod tempor incididunt ut labore et dolore magna aliqua. Ut enim ad minim veniam “</p>
  <svg class="abs" style="left:1073px;top:207px" width="14" height="20" viewBox="0 0 14 20"><path d="M3 2 L11 10 L3 18" fill="none" stroke="#1b1b1b" stroke-width="3.5"/></svg>
  <p class="abs posted center">POSTED ON MAY 30, 2019 / &nbsp;@verantelnews.com</p>
</section>

<footer class="abs footer">
  <div class="abs fcol" style="left:0;width:436px">
    <div class="abs foot-h" style="left:0;width:470px;top:48px;text-align:center">FOLLOW US OUT THERE</div>
    <span class="abs social" style="left:155px"></span>
    <span class="abs social" style="left:204px"></span>
    <span class="abs social" style="left:251px"></span>
    <span class="abs social" style="left:299px"></span>
  </div>
  <div class="abs fcol" style="left:436px;width:305px">
    <div class="abs flink" style="left:28px;top:60px">Home<br>About Us<br>Services &amp; Products</div>
    <div class="abs flink" style="left:207px;top:64px">Testimonials<br>Blog<br>Contact Us</div>
  </div>
  <div class="abs foot-h" style="left:893px;top:48px">NEWSLETTER</div>
  <div class="abs email">Enter Email id</div>
  <div class="abs btn submit">SUBMIT</div>
</footer>
<p class="abs copy center">© 2019 &nbsp;| &nbsp;www.verantelsite.com</p>

</body>
</html>
```